Business cards - BRENT Roofing & Siding

We need simple business cards made up for our Roofing & Siding business based in Calgary Alberta.
The logo on one side of the card and potentially our slogan "Built with trust, verified by time".
The other side could have:
-A small logo
-Rep name:
-Rep cell phone:
-Rep email:
-Office phone: 403-684-2093
-Website: PrairieShingleWorks.com

We would like to incorporate the colours from our logo, especially the lite blue on the jpeg file. I have attached the ai file and jpeg file. We like the colours better on the jpeg file.

I do not require a money back guarantee

```html
<!DOCTYPE html>
<html lang="en">
<head>
<meta charset="utf-8">
<title>BRENT Roofing &amp; Siding – Business Cards</title>
<link href="https://fonts.googleapis.com/css2?family=Montserrat:wght@400;500;600&display=swap" rel="stylesheet">
<style>
  :root {
    --stage: #1b1b1c;
    --card: #222223;
    --card-light: #2e2e30;
    --brand-blue: #1e8fe6;
    --white: #ffffff;
    --soft-white: #e6e6e6;
  }
  * { margin: 0; padding: 0; box-sizing: border-box; }
  html, body {
    width: 1200px; height: 900px; overflow: hidden;
    background: var(--stage);
    font-family: "Montserrat", sans-serif;
  }
  .stage { position: relative; width: 1200px; height: 900px; }
  .card {
    position: absolute; left: 290px;
    width: 620px; height: 354px;
    background: var(--card);
    overflow: hidden;
    box-shadow: 0 18px 40px rgba(0,0,0,.55);
  }
  .card--front { top: 60px; }
  .card--back { top: 486px; }
  .card__pattern {
    position: absolute; inset: 0;
    background: radial-gradient(ellipse at 55% 40%, var(--card-light) 0%, var(--card) 70%);
  }
  .brand-name {
    position: absolute;
    display: flex; align-items: center; gap: 12px;
    color: var(--white); font-weight: 600;
    letter-spacing: 2px; line-height: 1.15;
  }
  .brand-name__mark {
    flex: none; background: var(--brand-blue);
  }
  .card--front .brand-name {
    left: 0; right: 0; top: 150px; justify-content: center;
    font-size: 30px;
  }
  .card--front .brand-name__mark { width: 22px; height: 22px; }
  .card--back .brand-name {
    left: 40px; top: 150px; width: 250px;
    font-size: 22px;
  }
  .card--back .brand-name__mark { width: 16px; height: 16px; }
  .divider {
    position: absolute; left: 318px; top: 82px;
    width: 2px; height: 190px; background: var(--brand-blue);
  }
  .rep {
    position: absolute; left: 346px; top: 92px;
  }
  .rep__name {
    color: var(--brand-blue); font-weight: 600; font-size: 25px;
    letter-spacing: 1px; text-transform: uppercase;
  }
  .rep__title {
    color: var(--soft-white); font-size: 15px; letter-spacing: 1px;
    text-transform: uppercase; margin-top: 2px;
  }
  .contact-list { list-style: none; margin-top: 14px; }
  .contact-list li {
    display: flex; align-items: center; gap: 10px;
    color: var(--white); font-size: 16px; font-weight: 500;
    line-height: 27px;
  }
  .contact-list svg { width: 13px; height: 13px; flex: none; }
</style>
</head>
<body>
<main class="stage">

  <section class="card card--front" aria-label="Card front">
    <div class="card__pattern" role="img" aria-label="Faint dark maple leaf pattern background"></div>
    <div class="brand-name"><span class="brand-name__mark"></span>BRENT Roofing &amp; Siding</div>
  </section>

  <section class="card card--back" aria-label="Card back">
    <div class="card__pattern" role="img" aria-label="Faint dark maple leaf pattern background"></div>
    <div class="brand-name"><span class="brand-name__mark"></span>BRENT Roofing &amp; Siding</div>
    <div class="divider"></div>
    <div class="rep">
      <p class="rep__name">Daniel Korven</p>
      <p class="rep__title">Director</p>
      <ul class="contact-list">
        <li>
          <svg viewBox="0 0 16 16" fill="none" stroke="#1e8fe6" stroke-width="1.6"><path d="M4 1.5l2.5 3-1.5 1.8a9 9 0 004.7 4.7l1.8-1.5 3 2.5-1.5 2.5C7 14.5 1.5 9 1.5 3z"/></svg>
          403-684-2093
        </li>
        <li>
          <svg viewBox="0 0 16 16" fill="none" stroke="#1e8fe6" stroke-width="1.6"><rect x="4" y="1" width="8" height="14" rx="1.5"/><line x1="7" y1="12.5" x2="9" y2="12.5"/></svg>
          905-312-4870
        </li>
        <li>
          <svg viewBox="0 0 16 16" fill="none" stroke="#1e8fe6" stroke-width="1.6"><rect x="1" y="3" width="14" height="10" rx="1"/><path d="M1 3.5l7 5.5 7-5.5"/></svg>
          brentroof@prairiemail.net
        </li>
        <li>
          <svg viewBox="0 0 16 16" fill="none" stroke="#1e8fe6" stroke-width="1.4"><circle cx="8" cy="8" r="6.5"/><ellipse cx="8" cy="8" rx="3" ry="6.5"/><line x1="1.5" y1="8" x2="14.5" y2="8"/></svg>
          prairieshingleworks.com
        </li>
      </ul>
    </div>
  </section>

</main>
</body>
</html>
```